Modern design company business card design

We are a design oriented construction firm. The owner is an architect and licensed General Contractor and accomplished furniture designer. We do new home construction and large scale remodeling and office design. We would like a design for our new business cards that is clean and modern, but relatable. We like the bright green color of our logo mixed with different shades of grey. We're also open to reinterpreting the logo.

Target Market(s)

Potential design clients,
Construction clients

Industry/Entity Type

Architecture

Contact Information for Business Card

Tall Maple Design | Build Inc. (optional with logo, Inc. optional)Jeffrey MorganOwner (optional)317.555.0148 cell317.431.8056 officejmorgan@greensquareinc.comwww.greensquareinc.com

Font styles to use
Sans Serif
Other font styles liked:
• Avenir

Requirements
Nice to have
• I like designs that have some continuity between the front and back, i.e. similar layouts or graphic elements that wrap around the card. I tend to prefer horizontal over vertical, but that's not a have to. I also tend to prefer white or recycled paper.

```html
<!DOCTYPE html>
<html lang="en">
<head>
<meta charset="utf-8">
<title>Tall Maple Design | Build – Business Card</title>
<link rel="stylesheet" href="https://fonts.googleapis.com/css2?family=Nunito+Sans:wght@400;600;700&display=swap">
<style>
  :root {
    --bg: #e9e9e7;
    --card: #ffffff;
    --band-light: #c6de6a;
    --band-mid: #a6d463;
    --band-deep: #7cc35a;
    --name-green: #8cc63f;
    --grey-dark: #555555;
    --grey: #7d7d7d;
    --grey-light: #8a8a8a;
  }
  * { margin: 0; padding: 0; box-sizing: border-box; }
  html, body { width: 1200px; height: 900px; overflow: hidden; }
  body {
    background: var(--bg);
    font-family: "Nunito Sans", "Avenir", sans-serif;
    position: relative;
  }
  .card {
    position: absolute;
    width: 588px;
    height: 364px;
    background: var(--card);
    box-shadow: 0 6px 18px rgba(0,0,0,0.12);
    overflow: hidden;
  }
  .card--front { left: 77px; top: 29px; }
  .card--back  { left: 388px; top: 505px; }

  .band { position: absolute; left: 62px; width: 110px; }
  .band--top    { top: 0;     height: 70px;  background: var(--band-light); }
  .band--middle { top: 88px;  height: 110px; background: var(--band-mid); }
  .band--bottom { top: 216px; height: 148px; background: var(--band-deep); }

  .wordmark {
    position: absolute;
    left: 188px;
    top: 176px;
    color: var(--grey);
    font-size: 22px;
    font-weight: 600;
    line-height: 28px;
    white-space: nowrap;
  }
  .card--back .wordmark { top: 168px; }

  .holder { position: absolute; left: 184px; top: 18px; }
  .holder__name {
    color: var(--name-green);
    font-weight: 700;
    font-size: 20px;
    letter-spacing: 0.3px;
    line-height: 24px;
  }
  .holder__role { color: var(--grey-light); font-size: 16px; line-height: 22px; }

  .contacts { position: absolute; left: 188px; top: 239px; list-style: none; }
  .contacts__item {
    display: flex;
    align-items: center;
    height: 24.7px;
    color: var(--grey-dark);
    font-size: 16px;
  }
  .contacts__icon { width: 13px; height: 13px; margin-right: 10px; fill: var(--name-green); }
</style>
</head>
<body>

  <section class="card card--front" aria-label="Business card front">
    <div class="band band--top"></div>
    <div class="band band--middle"></div>
    <div class="band band--bottom"></div>

    <div class="holder">
      <p class="holder__name">DENNIS HOLLOWAY</p>
      <p class="holder__role">Owner</p>
    </div>

    <p class="wordmark">Tall Maple Design | Build</p>

    <ul class="contacts">
      <li class="contacts__item">
        <svg class="contacts__icon" viewBox="0 0 16 16" aria-hidden="true"><path d="M3.5 1l2.4 2.9-1.3 1.8c.9 2 2.6 3.7 4.7 4.7l1.8-1.3L14 11.5 12.6 14C6.8 13.6 2.4 9.2 2 3.4z"/></svg>
        317.555.0172
      </li>
      <li class="contacts__item">
        <svg class="contacts__icon" viewBox="0 0 16 16" aria-hidden="true"><path d="M4.5 1h7a1 1 0 0 1 1 1v12a1 1 0 0 1-1 1h-7a1 1 0 0 1-1-1V2a1 1 0 0 1 1-1zm.6 1.8v8.6h5.8V2.8zM8 12.4a.8.8 0 1 0 0 1.6.8.8 0 0 0 0-1.6z"/></svg>
        317.555.0148
      </li>
      <li class="contacts__item">
        <svg class="contacts__icon" viewBox="0 0 16 16" aria-hidden="true"><path d="M1 3.5h14v9H1zm1.6 1.2L8 9l5.4-4.3z"/></svg>
        dholloway@tallmapleinc.example
      </li>
      <li class="contacts__item">
        <svg class="contacts__icon" viewBox="0 0 16 16" aria-hidden="true"><path d="M6.6 9.4l2.8-2.8 1 1-2.8 2.8zM9 3.2l1.6-1.6a2.8 2.8 0 0 1 4 4L13 7.2l-1-1 1.6-1.6a1.4 1.4 0 0 0-2-2L10 4.2zM7 12.8l-1.6 1.6a2.8 2.8 0 0 1-4-4L3 8.8l1 1-1.6 1.6a1.4 1.4 0 0 0 2 2L6 11.8z"/></svg>
        www.tallmapleinc.example
      </li>
    </ul>
  </section>

  <section class="card card--back" aria-label="Business card back">
    <div class="band band--top"></div>
    <div class="band band--middle"></div>
    <div class="band band--bottom"></div>

    <p class="wordmark">Tall Maple Design | Build</p>
  </section>

</body>
</html>
```